Website Redesign for MarrowArc.co.za – Bold, Modern & Professional Tattoo Supply Store (B2B ...

We’re looking for a skilled and creative web designer to redesign MarrowArc.co.za, a leading tattoo equipment and supplies store based in South Africa. The business serves both B2B (tattoo studios, artists, wholesalers) and B2C (individual customers) markets.

The current website is outdated and lacks the modern, edgy look that reflects the tattoo industry. We want a fresh, bold, and professional design that appeals to both professional artists and retail customers — combining trust, style, and functionality.

About the Business:
Marrow Arc supplies a wide range of tattoo-related products, including machines, needles, inks, hygiene supplies, and accessories. The company is well-established in the South African market and serves both individual tattoo artists and studios, as well as end customers looking for quality equipment.

The website must reflect the creative, bold, and artistic nature of the tattoo industry, while still being easy to navigate, fast, and conversion-focused.

What We’re Looking For:
A bold, modern design with a clear structure
Strong visual identity that reflects the tattoo culture — edgy, artistic, but still clean and professional
A layout that works for both B2B and B2C audiences
Clear product presentation and strong CTAs (Buy Now, Request Quote, Contact, etc.)
Fully responsive design (desktop + mobile)
Easy-to-navigate product categories and filters
Space for featured products, promotions, and artist-focused content
Integration of trust elements (payment icons, reviews, certifications, etc.)

Pages We Need Designed:
Homepage
Product detail page

Inspiration / Style Direction:
We’re looking for something with a strong personality, inspired by tattoo culture, but still clean and user-friendly. Think:

Dark theme with bold highlights (but open to light themes if well executed)
High-quality visuals and product imagery

Examples for inspiration:
GrimQuill.co.uk
Wexley RPN
Corvane Needle Supply
Brisk Tallow

Deliverables:
Full desktop and mobile designs (Figma, XD, or PSD)
All design source files
Fonts, icons, and assets used
Clearly labeled layers and organized files
Ready for development handoff

Target Market(s)

MarrowArc.co.za targets both B2B and B2C customers in South Africa: B2B: Professional tattoo artists, studios, and wholesalers looking for high-quality, reliable equipment and bulk pricing. B2C: Individual customers, hobbyists, and beginners seeking safe, affordable tattoo supplies with guidance and support. The site should appeal to both experienced professionals and newcomers, combining a bold, authentic tattoo vibe with a clean, user-friendly shopping experience.

Industry/Entity Type

Tattoo Equipment & Supplies – E-commerce (B2B & B2C)

Number of Pages Required

2 page

Requirements
Must have
• Responsive design, bold tattoo-inspired visual style, clear navigation for B2B & B2C, strong product presentation, clear call-to-actions, trust elements (reviews, badges, payment icons), category filters & search, dedicated B2B/wholesale info page, speed-optimized layout, easy access to contact & support.
Should not have
• Overly complex animations, cluttered layout, generic stock images, too many fonts or colors, hidden navigation, auto-play videos or sounds, outdated visual styles, low-quality product images, confusing checkout process, unnecessary pop-ups.

```html
<!DOCTYPE html>
<html lang="en">
<head>
<meta charset="utf-8">
<title>Marrow Arc – Tattoo Supplies</title>
<link href="https://fonts.googleapis.com/css2?family=Syne:wght@500;600;700&family=Urbanist:wght@400;500;600&display=swap" rel="stylesheet">
<style>
:root{
  --bg:#0b0a09;
  --bg-band:#121110;
  --panel:#0f0e0d;
  --card:#151311;
  --line:#2b2621;
  --gold:#b58a4e;
  --gold-dark:#9c7640;
  --text:#ece6dc;
  --muted:#bdb5a8;
  --white:#ffffff;
}
*{box-sizing:border-box;margin:0;padding:0}
html,body{width:1200px;height:3942px;overflow:hidden;background:var(--bg)}
body{position:relative;font-family:"Urbanist",sans-serif;color:var(--text)}
.abs{position:absolute}
.head-font{font-family:"Syne",sans-serif;font-weight:600;letter-spacing:.5px;text-transform:uppercase}
.gold{color:var(--gold)}
.btn{position:absolute;display:flex;align-items:center;justify-content:center;border-radius:30px;font-size:14px;text-transform:uppercase;font-weight:500;letter-spacing:.3px}
.btn-solid{background:var(--gold);color:#1a140c}
.btn-line{border:1.5px solid var(--gold);color:var(--gold)}

/* header */
.site-header{left:0;top:0;width:1200px;height:97px;background:#000}
.brand{font-family:"Urbanist",sans-serif;font-weight:600;font-size:24px;color:var(--white);letter-spacing:1px}
.search{left:602px;top:31px;width:304px;height:38px;border:1px solid #3a3a3a;border-radius:4px;font-size:11px;color:#8a8a8a;padding:12px 14px;text-transform:uppercase}
.icon-box{top:31px;width:38px;height:38px;border:1px solid #3a3a3a;border-radius:4px;display:flex;align-items:center;justify-content:center}
.main-nav{left:0;top:97px;width:1200px;height:41px;background:#0a0a0a;border-bottom:1px solid #1a1a1a}
.main-nav span{position:absolute;top:13px;font-size:12.5px;font-weight:500;text-transform:uppercase;color:var(--white)}
.main-nav .active{color:var(--gold)}

/* hero */
.hero{left:0;top:138px;width:1200px;height:451px;background:linear-gradient(90deg,#1c1b1a 0%,#141312 55%,#0c0c0c 100%)}
.hero-photo{right:0;top:0;width:420px;height:451px;background:radial-gradient(ellipse at 60% 35%,#5a5a5a 0%,#2a2a2a 35%,#111 75%)}
.hero h1{left:119px;top:88px;font-size:30px;line-height:52px;font-weight:600}
.hero p{left:119px;top:205px;width:470px;font-size:16px;line-height:39px;color:var(--text)}

/* about */
.about-frame{left:112px;top:670px;width:482px;height:515px;border:1.5px solid var(--gold)}
.about-photo{left:121px;top:679px;width:473px;height:506px;background:linear-gradient(135deg,#3a2a22 0%,#6b4a38 40%,#8a6148 60%,#2a1d18 100%)}
.about h2{left:661px;top:680px;font-size:29px}
.about p{left:661px;width:430px;font-size:15px;line-height:34.3px}

/* products */
.products-panel{left:112px;top:1270px;width:976px;height:969px;background:var(--panel);border-radius:24px}
.section-title{left:0;width:1200px;text-align:center;font-size:30px}
.p-card{width:291px;height:322px;background:var(--card);border:1px solid var(--line);border-radius:14px}
.p-img{position:absolute;left:14px;top:12px;width:263px;height:213px;background:var(--white)}
.p-fill{position:absolute;left:30px;top:30px;width:203px;height:153px;border-radius:6px}
.heart{position:absolute;right:10px;top:12px;width:34px;height:34px;border-radius:6px;background:var(--gold);display:flex;align-items:center;justify-content:center}
.p-name{position:absolute;left:10px;right:10px;top:245px;text-align:center;color:var(--gold);font-size:13.5px;line-height:31px;text-transform:uppercase}

/* categories */
.c-card{top:2412px;width:222px;height:201px;background:#131211;border:1px solid #1f1d1b;border-radius:12px}
.c-icon{position:absolute;left:76px;top:22px;width:70px;height:100px;border-radius:8px}
.c-name{position:absolute;left:0;width:100%;top:152px;text-align:center;font-size:15px;font-weight:500;text-transform:uppercase}
.arrow{top:2498px;width:28px;height:28px;border:1.5px solid var(--white);border-radius:50%;display:flex;align-items:center;justify-content:center}

/* reviews */
.stars{left:0;width:1200px;top:2760px;text-align:center;color:var(--gold);font-size:20px;letter-spacing:4px}
.quote-head{left:0;width:1200px;top:2815px;text-align:center;color:var(--gold);font-size:12px;text-transform:uppercase}
.quote{left:180px;width:840px;top:2856px;text-align:center;font-size:15px;line-height:34px}
.quote-by{left:0;width:1200px;top:2941px;text-align:center;color:var(--gold);font-size:12px;text-transform:uppercase}
.dots{left:555px;top:2996px;display:flex;gap:16px}
.dots i{display:block;width:9px;height:9px;border-radius:50%;border:1.5px solid #777}
.dots i.on{background:var(--gold);border-color:var(--gold)}

/* promo */
.lower-band{left:0;top:3230px;width:1200px;height:712px;background:var(--bg-band)}
.promo{left:138px;top:3092px;width:924px;height:272px;background:radial-gradient(ellipse at 50% 40%,#bf9558,#a8804a);border-radius:26px}
.promo h3{position:absolute;left:0;width:100%;top:54px;text-align:center;font-size:25px;color:var(--white)}
.promo p{position:absolute;left:0;width:100%;top:109px;text-align:center;font-size:15px;color:var(--white)}
.promo .btn{left:358px;top:170px;width:208px;height:41px;background:var(--white);color:var(--gold-dark)}

/* footer */
.foot-brand{left:0;width:1200px;top:3455px;text-align:center;font-size:34px}
.foot-col h4{font-family:"Syne",sans-serif;font-weight:600;font-size:18px;color:var(--gold);text-transform:uppercase}
.foot-col ul{list-style:none;margin-top:20px}
.foot-col li{font-size:11.5px;text-transform:uppercase;line-height:31.6px;color:var(--white)}
.pay{top:3808px;width:41px;height:29px;border-radius:4px}
.copyright{left:0;width:1200px;top:3903px;text-align:center;font-size:13px;text-transform:uppercase}
</style>
</head>
<body>

<header class="abs site-header">
  <div class="abs brand" style="left:112px;top:33px">MARROW ARC</div>
  <div class="abs search">Search here...
    <svg class="abs" style="right:14px;top:13px" width="12" height="12" viewBox="0 0 12 12"><circle cx="5" cy="5" r="3.8" fill="none" stroke="#8a8a8a" stroke-width="1.3"/><path d="M8 8l3 3" stroke="#8a8a8a" stroke-width="1.3"/></svg>
  </div>
  <div class="abs icon-box" style="left:930px"><svg width="16" height="14" viewBox="0 0 16 14"><path d="M8 13S1 8.5 1 4.5A3.3 3.3 0 0 1 8 3a3.3 3.3 0 0 1 7 1.5C15 8.5 8 13 8 13z" fill="none" stroke="#fff" stroke-width="1.2"/></svg></div>
  <div class="abs icon-box" style="left:990px"><svg width="14" height="16" viewBox="0 0 14 16"><circle cx="7" cy="5" r="3.2" fill="none" stroke="#fff" stroke-width="1.2"/><path d="M1 15c0-3.5 2.7-5.5 6-5.5s6 2 6 5.5" fill="none" stroke="#fff" stroke-width="1.2"/></svg></div>
  <div class="abs icon-box" style="left:1049px"><svg width="14" height="16" viewBox="0 0 14 16"><rect x="1.5" y="5" width="11" height="10" fill="none" stroke="#fff" stroke-width="1.2"/><path d="M4.5 5V3.5a2.5 2.5 0 0 1 5 0V5" fill="none" stroke="#fff" stroke-width="1.2"/></svg></div>
</header>

<nav class="abs main-nav">
  <span class="active" style="left:144px">Home</span>
  <span style="left:236px">About Us</span>
  <span style="left:357px">Featured Products</span>
  <span style="left:554px">Our Catagories</span>
  <span style="left:721px">Reviews</span>
  <span style="left:834px">Accesories</span>
  <span style="left:969px">Contact Us</span>
</nav>

<section class="abs hero">
  <div class="abs hero-photo" role="img" aria-label="Gloved hand holding a rotary tattoo machine"></div>
  <h1 class="abs head-font">Fuel your <span class="gold">art with gear</span><br>you can trust</h1>
  <p class="abs">Pro-grade machines, needles, inks and studio essentials —<br>built for serious artists.</p>
  <div class="btn btn-solid" style="left:119px;top:314px;width:164px;height:42px">Shop Pro Gear</div>
  <div class="btn btn-line" style="left:308px;top:314px;width:182px;height:42px">Request a Quote</div>
</section>

<section class="about">
  <div class="abs about-frame"></div>
  <div class="abs about-photo" role="img" aria-label="Tattoo artist in black gloves inking script lettering on skin"></div>
  <h2 class="abs head-font">About <span class="gold">MarrowArc</span></h2>
  <p class="abs" style="top:748px">MarrowArc is a professional tattoo equipment supplier based in Pretoria, South Africa. We provide high-quality machines, cartridges, traditional needles, inks, grips, and studio essentials to artists and studios nationwide. Our focus is reliability, safety, and service.</p>
  <p class="abs" style="top:944px">We support professional artists and studios across South Africa with gear that meets strict performance and hygiene standards. Expect fast service, clear product info, and honest advice.</p>
  <div class="btn btn-solid" style="left:661px;top:1113px;width:149px;height:41px">Learn More</div>
</section>

<section>
  <div class="abs products-panel"></div>
  <h2 class="abs head-font section-title" style="top:1326px">MarrowArc <span class="gold">Products</span></h2>

  <div class="abs p-card" style="left:139px;top:1410px">
    <div class="p-img"><div class="p-fill" role="img" aria-label="Rolls of blue sterilisation reel" style="background:linear-gradient(135deg,#9ed3ea,#5fb0d6)"></div></div>
    <div class="heart"><svg width="16" height="14" viewBox="0 0 16 14"><path d="M8 13S1 8.5 1 4.5A3.3 3.3 0 0 1 8 3a3.3 3.3 0 0 1 7 1.5C15 8.5 8 13 8 13z" fill="#fff"/></svg></div>
    <div class="p-name">Cleanspool 100 mm x 100m –<br>Sterilization</div>
  </div>
  <div class="abs p-card" style="left:455px;top:1410px">
    <div class="p-img"><div class="p-fill" role="img" aria-label="Steel ring opening pliers" style="background:linear-gradient(135deg,#f4f4f4,#c9c9c9)"></div></div>
    <div class="heart"><svg width="16" height="14" viewBox="0 0 16 14"><path d="M8 13S1 8.5 1 4.5A3.3 3.3 0 0 1 8 3a3.3 3.3 0 0 1 7 1.5C15 8.5 8 13 8 13z" fill="#fff"/></svg></div>
    <div class="p-name">5 3/4" Ring Opening Pliers –<br>Piercing Tools</div>
  </div>
  <div class="abs p-card" style="left:770px;top:1410px">
    <div class="p-img"><div class="p-fill" role="img" aria-label="Black outlining ink bottle" style="background:radial-gradient(circle,#2a2a2a,#6a6a6a 60%,#fff 80%)"></div></div>
    <div class="heart"><svg width="16" height="14" viewBox="0 0 16 14"><path d="M8 13S1 8.5 1 4.5A3.3 3.3 0 0 1 8 3a3.3 3.3 0 0 1 7 1.5C15 8.5 8 13 8 13z" fill="#fff"/></svg></div>
    <div class="p-name">Nokuro Dusk Tattoo Ink –<br>Outlining Ink</div>
  </div>

  <div class="abs p-card" style="left:139px;top:1763px">
    <div class="p-img"><div class="p-fill" role="img" aria-label="Smoke grey tattoo ink bottle" style="background:linear-gradient(180deg,#5a7aa3,#e0892e)"></div></div>
    <div class="heart"><svg width="16" height="14" viewBox="0 0 16 14"><path d="M8 13S1 8.5 1 4.5A3.3 3.3 0 0 1 8 3a3.3 3.3 0 0 1 7 1.5C15 8.5 8 13 8 13z" fill="#fff"/></svg></div>
    <div class="p-name">Everline Tattoo Ink –<br>Smoke 2oz</div>
  </div>
  <div class="abs p-card" style="left:455px;top:1763px">
    <div class="p-img"><div class="p-fill" role="img" aria-label="Disposable silicone gel grips with clear tips" style="background:linear-gradient(135deg,#f2f2f2,#3a3a3a 50%,#e8e8e8)"></div></div>
    <div class="heart"><svg width="16" height="14" viewBox="0 0 16 14"><path d="M8 13S1 8.5 1 4.5A3.3 3.3 0 0 1 8 3a3.3 3.3 0 0 1 7 1.5C15 8.5 8 13 8 13z" fill="#fff"/></svg></div>
    <div class="p-name">Disposable Silica Gel Grip<br>(Clear Tip) 25mm</div>
  </div>
  <div class="abs p-card" style="left:770px;top:1763px">
    <div class="p-img"><div class="p-fill" role="img" aria-label="Transparent blue tattoo needle cartridge" style="background:linear-gradient(135deg,#ffffff,#a9d4ee 55%,#ffffff)"></div></div>
    <div class="heart"><svg width="16" height="14" viewBox="0 0 16 14"><path d="M8 13S1 8.5 1 4.5A3.3 3.3 0 0 1 8 3a3.3 3.3 0 0 1 7 1.5C15 8.5 8 13 8 13z" fill="#fff"/></svg></div>
    <div class="p-name">QTR Tattoo Liner<br>Cartridges</div>
  </div>

  <div class="btn btn-solid" style="left:419px;top:2135px;width:216px;height:42px">View More Products</div>
  <div class="btn btn-line" style="left:658px;top:2135px;width:121px;height:42px">Buy Now</div>
</section>

<section>
  <h2 class="abs head-font section-title" style="top:2318px">MarrowArc <span class="gold">Categories</span></h2>
  <div class="abs arrow" style="left:35px"><svg width="10" height="10" viewBox="0 0 10 10"><path d="M6.5 1.5L3 5l3.5 3.5" fill="none" stroke="#fff" stroke-width="1.3"/></svg></div>
  <div class="abs arrow" style="left:1127px"><svg width="10" height="10" viewBox="0 0 10 10"><path d="M3.5 1.5L7 5 3.5 8.5" fill="none" stroke="#fff" stroke-width="1.3"/></svg></div>
  <div class="abs c-card" style="left:110px"><div class="c-icon" role="img" aria-label="Tattoo ink bottle" style="left:96px;width:30px;background:linear-gradient(180deg,#666,#1b1b1b)"></div><div class="c-name">Special Tatoo Ink</div></div>
  <div class="abs c-card" style="left:363px"><div class="c-icon" role="img" aria-label="Mixing solution bottle" style="left:94px;width:34px;background:linear-gradient(180deg,#fff,#ddd)"></div><div class="c-name">Mixing Solutions</div></div>
  <div class="abs c-card" style="left:614px"><div class="c-icon" role="img" aria-label="Autoclave steriliser unit" style="left:60px;width:102px;height:96px;background:linear-gradient(180deg,#f2f2f2,#bcbcbc)"></div><div class="c-name">Medical Supplies</div></div>
  <div class="abs c-card" style="left:866px"><div class="c-icon" role="img" aria-label="Tattoo needle cartridge" style="left:70px;width:82px;height:90px;background:linear-gradient(135deg,#ddd,#777)"></div><div class="c-name">Needles</div></div>
</section>

<section>
  <h2 class="abs head-font section-title" style="top:2692px">Our <span class="gold">Reviews</span></h2>
  <div class="abs stars">★★★★★</div>
  <div class="abs quote-head">"The only supplier we trust for studio-grade equipment."</div>
  <p class="abs quote">We've been ordering machines, cartridges, and ink sets from Marrow Arc for years. Their products are consistent, authentic, and always delivered fast. As a busy studio, reliability is everything — they've never let us down.</p>
  <div class="abs quote-by">– Needle Row Studio, Cape Town</div>
  <div class="abs dots"><i class="on"></i><i></i><i></i><i></i></div>
</section>

<div class="abs lower-band"></div>
<section class="abs promo">
  <h3 class="head-font">New Machines Just Dropped</h3>
  <p>Latest wireless pens, rotary machines &amp; power supplies — fresh stock, limited quantities.</p>
  <div class="btn">Shop New Arrivals</div>
</section>

<footer>
  <div class="abs brand foot-brand">MARROW ARC</div>
  <div class="abs foot-col" style="left:110px;top:3557px">
    <h4>Information</h4>
    <ul><li>Track My Parcel</li><li>Delivery Information</li><li>About Us</li><li>Privacy Policy (POPI)</li><li>Terms &amp; Conditions</li><li>Original Manufacturers Guarantee</li><li>Cookies Policy</li><li>Returns &amp; Refunds Policy</li></ul>
  </div>
  <div class="abs foot-col" style="left:571px;top:3557px">
    <h4>Customer Service</h4>
    <ul><li>Contact Us</li><li>Returns</li><li>Site Map</li></ul>
  </div>
  <div class="abs foot-col" style="left:963px;top:3557px">
    <h4>My Account</h4>
    <ul><li>Account</li><li>Order History</li><li>Wish List (0)</li><li>Newsletter</li></ul>
  </div>
  <div class="abs" style="left:666px;top:3808px;width:114px;height:29px;background:#fff;border-radius:3px;color:#111;font-size:17px;font-weight:500;display:flex;align-items:center;justify-content:center">Credora</div>
  <div class="abs pay" style="left:798px;background:#2e4a8a"></div>
  <div class="abs pay" style="left:848px;background:#e6e6e6"></div>
  <div class="abs pay" style="left:897px;background:#f4f4f4"></div>
  <div class="abs pay" style="left:947px;background:#2a74c9"></div>
  <div class="abs pay" style="left:996px;background:#2e4a8a"></div>
  <div class="abs pay" style="left:1046px;background:#2b63c6"></div>
  <div class="abs copyright">MarrowArc Pty Ltd © 2025 | Development by Dunmore Dev</div>
</footer>

</body>
</html>
```